Stationery Design Project for Marketing Consultancy

I have started a new consultancy business and require the following elements to be designed using existing logo:
• Business card
• Letterhead
• Envelope (DL, C4, C5)
• Microsoft word template for report writing
• A4 Presentation Folder
• Powerpoint template
COPY FOR FRONT AND BACK OF BUSINESS CARD
logo
'Measurable Marketing. Epic Results' slogan (but no need to use existing lockup with logo)
name, B Bus. Mktg, Grad Dip Digital Mktg, CPM (post nominal abbreviations in smaller font)
mobile: 04XX-XXX-XXX (I will give details to the winner to add)
website: www.tolvarin.com.au
email: info@tolvarin.com.au
COPY FOR LETTERHEAD
Logo
Company Name
Please, submit your designs that include business card, letterhead and envelope. Once selected the winner will be asked to complete the project by creating the rest of the artwork.
FINAL FILES
Print ready files to be supplied as well as Indesign files so that minor amends can be made if necessary in future.
• Layered vectors in EPS & PDF
• Screen quality JPEG & PNGs
ABOUT THE BUSINESS: TOLVARIN
I work with clients to understand their business challenges, developing and executing measurable marketing strategies tied to key business metrics. Services include:
Services include:
• Business planning and business development
• Marketing and brand strategy
• Insight-driven integrated campaigns
• Loyalty programs and retention marketing
• Marketing automation
• Direct marketing (traditional and digital)
• Content strategy and development
Hi everyone,
Target Market(s)
Corporate decision makers (heads of marketing, general managers etc) and small to medium sized business owners. Predominately male aged 35+
Industry/Entity Type
Marketing
Requirements
Must have
- BRAND PERSONALITY
The successful design will communicate brand personality. I am a professional, results-driven entrepreneur, but want to show off my creative flair.
MEMORABILITY
Looking for a unique and eye-catching design. Am considering special printing effects (die cuts, letterpress, interactive elements, embossing, foiling etc) or a striking minimalist approach.
Nice to have
- I have a mission that could be incorporated on reverse if room -
Turning insights into actions & passion into profit.
Should not have
- Use of pink or green.

```html
<!DOCTYPE html>
<html lang="en">
<head>
<meta charset="utf-8">
<title>Tolvarin Business Card</title>
<link href="https://fonts.googleapis.com/css2?family=Source+Sans+3:wght@400;600&display=swap" rel="stylesheet">
<style>
  :root {
    --page: #ffffff;
    --card-light: #f1f1f1;
    --card-dark-a: #2a2a2a;
    --card-dark-b: #1b1b1b;
    --ink: #1e1e1e;
    --ink-soft: #333333;
    --accent: #f04e0f;
    --mark-light: #f4f4f4;
    --mark-faint: #d6dcdc;
  }
  * { margin: 0; padding: 0; box-sizing: border-box; }
  html, body {
    width: 1200px; height: 907px; overflow: hidden;
    background: var(--page);
    font-family: "Source Sans 3", "Myriad Pro", Arial, sans-serif;
    color: var(--ink);
  }
  .canvas { position: relative; width: 1200px; height: 907px; }

  .card { position: absolute; left: 300px; width: 600px; height: 352px; background: var(--card-light); overflow: hidden; }
  .card--front { top: 78px; }
  .card--back { top: 476px; }

  .brand-panel {
    position: absolute; left: 0; top: 0; width: 353px; height: 100%;
    background: linear-gradient(135deg, var(--card-dark-a), var(--card-dark-b));
  }
  .brand-dot {
    position: absolute; left: 136px; top: 96px; width: 80px; height: 80px;
    border-radius: 50%; background: var(--mark-light);
  }
  .brand-name {
    position: absolute; left: 0; top: 222px; width: 353px; text-align: center;
    font-size: 46px; font-weight: 600; letter-spacing: 2px; color: var(--mark-light);
  }

  .slogan { position: absolute; left: 384px; top: 214px; color: var(--ink); }
  .slogan__lead { font-size: 16.5px; line-height: 22px; }
  .slogan__main { font-size: 27px; line-height: 36px; letter-spacing: 1.2px; }

  .contact { position: absolute; left: 50px; top: 142px; }
  .contact__name { font-size: 17px; color: var(--accent); }
  .contact__name strong { font-weight: 600; }
  .contact__creds { margin-top: 5px; font-size: 10px; color: var(--ink-soft); }
  .contact__list { list-style: none; margin-top: 24px; font-size: 16px; line-height: 22.5px; }
  .contact__label { display: inline-block; width: 24px; font-weight: 600; color: var(--accent); }

  .faint-mark {
    position: absolute; left: 375px; top: 88px; width: 110px; height: 110px;
    border-radius: 50%; background: var(--mark-faint);
  }
  .mission { position: absolute; left: 331px; top: 226px; color: var(--ink); line-height: 23px; }
  .mission__line1 { font-size: 15px; }
  .mission__line2 { font-size: 17px; }
</style>
</head>
<body>
<main class="canvas">
  <section class="card card--front" aria-label="Business card front">
    <div class="brand-panel">
      <span class="brand-dot" aria-hidden="true"></span>
      <p class="brand-name">TOLVARIN</p>
    </div>
    <div class="slogan">
      <p class="slogan__lead">Measurable Marketing.</p>
      <p class="slogan__main">Epic Results.</p>
    </div>
  </section>

  <section class="card card--back" aria-label="Business card back">
    <div class="contact">
      <p class="contact__name"><strong>Liam</strong> Hartley</p>
      <p class="contact__creds">B Bus. Mktg, Grad Dip Digital Mktg, CPM</p>
      <ul class="contact__list">
        <li><span class="contact__label">M</span>0400 555 318</li>
        <li><span class="contact__label">W</span>www.tolvarin.com.au</li>
        <li><span class="contact__label">E</span>info@tolvarin.com.au</li>
      </ul>
    </div>
    <span class="faint-mark" aria-hidden="true"></span>
    <div class="mission">
      <p class="mission__line1">Turning insights into action</p>
      <p class="mission__line2">and passion into profit.</p>
    </div>
  </section>
</main>
</body>
</html>
```